Business card design for holistic health care clinic

We need a double-sided business card design for our holistic health care clinic that integrates our logo design and also its color scheme. My business is called Valmira. It is an integrative medicine clinic. You have already done the logo for me. Please ensure an elegant and upscale design that is not cluttered, but still has all the necessary information (please see below for details).

Target Market(s)

Wellness, fitness, rehabilitation for educated, well-traveled open-minded clients who are focused on natural, organic, balanced and preventive healthcare and lifestyle.

Industry/Entity Type

Medical

Contact Information for Business Card

Modern, clean.

Number of Pages Required

1 page

Font styles to use
Serif
Sans Serif

Colors

Designer to choose colors to be used in the design.

Requirements
Must have
• Logo on one side, all other information on the other side.
• Other information should include:
• Tobias Wrenfeld - DOE, CPT, LMT
• 4100 East Marrow Drive
• Austin, TX 78119
• 512 555 0148
• 818 555 0192
• info@ValmiraHealth.example
• t.wrenfeld@ValmiraHealth.example
Nice to have
• Darker background on front - but not totally black - shaded/dark gray.

```html
<!DOCTYPE html>
<html lang="en">
<head>
<meta charset="utf-8">
<title>Valmira Business Card</title>
<link href="https://fonts.googleapis.com/css2?family=Roboto:wght@400;500;700&family=Roboto+Condensed:wght@700&display=swap" rel="stylesheet">
<style>
  :root {
    --backdrop: #5a4838;
    --card-dark: #262627;
    --card-dark-edge: #2e2e2f;
    --brand-blue: #0a8fcb;
    --wave-blue: #0b8fca;
    --wave-gray: #a9a9aa;
    --text-light: #ececec;
    --white: #ffffff;
  }
  * { margin: 0; padding: 0; box-sizing: border-box; }
  html, body { width: 1200px; height: 960px; overflow: hidden; }
  body {
    background: var(--backdrop);
    font-family: "Roboto", Arial, sans-serif;
    position: relative;
  }
  .card {
    position: absolute;
    width: 600px;
    height: 344px;
    border-radius: 18px;
    overflow: hidden;
    background: linear-gradient(180deg, var(--card-dark) 0%, var(--card-dark-edge) 100%);
  }
  .card--front { left: 315px; top: 113px; }
  .card--back { left: 312px; top: 472px; }

  .wave { position: absolute; inset: 0; }

  .brand-name {
    position: absolute;
    font-family: "Roboto", Arial, sans-serif;
    font-weight: 700;
    color: var(--brand-blue);
    letter-spacing: 1px;
    line-height: 1;
  }
  .card--front .brand-name { left: 34px; top: 72px; font-size: 48px; }
  .card--back .brand-name { left: 0; right: 0; top: 138px; text-align: center; font-size: 64px; }

  .address {
    position: absolute;
    left: 34px; top: 184px;
    font-size: 14px;
    line-height: 18px;
    font-style: normal;
    color: var(--text-light);
  }
  .contact-list {
    position: absolute;
    left: 34px; top: 231px;
    list-style: none;
    font-size: 14px;
    color: var(--text-light);
  }
  .contact-list li {
    display: flex;
    align-items: center;
    height: 19px;
  }
  .contact-icon {
    width: 14px; height: 14px;
    margin-right: 9px;
    fill: var(--brand-blue);
    flex: none;
  }
  .holder {
    position: absolute;
    right: 28px; top: 258px;
    text-align: right;
    color: var(--white);
    font-family: "Roboto Condensed", "Arial Narrow", sans-serif;
    font-weight: 700;
    white-space: nowrap;
  }
  .holder-name { font-size: 19px; letter-spacing: 0.2px; }
  .holder-credentials { font-size: 12px; margin-left: 3px; }

  .tagline {
    position: absolute;
    left: 0; right: 0; top: 280px;
    text-align: center;
    font-size: 14.5px;
    color: var(--white);
  }
</style>
</head>
<body>

<section class="card card--front" aria-label="Business card front">
  <svg class="wave" viewBox="0 0 600 344" width="600" height="344" aria-hidden="true">
    <path d="M150 344 C 300 336, 355 270, 395 150 C 430 45, 480 4, 580 0 L600 0 L600 344 Z" fill="var(--wave-gray)"/>
    <path d="M175 344 C 320 336, 372 272, 410 160 C 445 55, 490 8, 585 0 L600 0 L600 344 Z" fill="var(--wave-blue)"/>
  </svg>

  <div class="brand-name">VALMIRA</div>

  <address class="address">
    4100 East Marrow Drive<br>
    Austin, TX 78119
  </address>

  <ul class="contact-list">
    <li>
      <svg class="contact-icon" viewBox="0 0 24 24" aria-hidden="true"><path d="M6.6 10.8a15.1 15.1 0 0 0 6.6 6.6l2.2-2.2c.3-.3.7-.4 1-.2 1.1.4 2.3.6 3.6.6.6 0 1 .4 1 1V20c0 .6-.4 1-1 1C10.6 21 3 13.4 3 4c0-.6.4-1 1-1h3.5c.6 0 1 .4 1 1 0 1.3.2 2.5.6 3.6.1.3 0 .7-.2 1z"/></svg>
      512 555 0148
    </li>
    <li>
      <svg class="contact-icon" viewBox="0 0 24 24" aria-hidden="true"><path d="M7 1h10a2 2 0 0 1 2 2v18a2 2 0 0 1-2 2H7a2 2 0 0 1-2-2V3a2 2 0 0 1 2-2zm0 3v14h10V4zm5 15.5a1 1 0 1 0 0 2 1 1 0 0 0 0-2z"/></svg>
      818 555 0192
    </li>
    <li>
      <svg class="contact-icon" viewBox="0 0 24 24" aria-hidden="true"><path d="M3 5h18v2l-9 6-9-6zm0 4 9 6 9-6v10H3z"/></svg>
      t.wrenfeld@ValmiraHealth.example
    </li>
    <li>
      <svg class="contact-icon" viewBox="0 0 24 24" aria-hidden="true"><circle cx="12" cy="12" r="10"/></svg>
      www.ValmiraHealth.example
    </li>
  </ul>

  <div class="holder">
    <span class="holder-name">TOBIAS WRENFELD</span><span class="holder-credentials">- DOE, CPT, LMT</span>
  </div>
</section>

<section class="card card--back" aria-label="Business card back">
  <div class="brand-name">VALMIRA</div>
  <p class="tagline">it’s all about you – your health, your objectives</p>
</section>

</body>
</html>
```